Casino with the 'highest winning percentage' needs a stationery design

This is for a casino in Colombo, Sri Lanka and we need a stationery design for business card, letter head and envelope.

Should be very professional, simple and elegant without fancy fonts

Reason: Not fully satisfied with the designs. Need more designs.

Business

• 1. card deck symbol 'CLUBS' in red, or black

2. name in BLOCK CAPITAL LETTERS

3. Preferred font colours are black, white or red

4. Prefer 'professional /elegant' fonts
• SHOULD NOT HAVE ANY OTHER SYMBOL EXCEPT 'CLUBS'

DO NOT PREFER ITALIC FONTS

```html
<!DOCTYPE html>
<html lang="en">
<head>
<meta charset="utf-8">
<title>Corvan's Entertainment — Letterhead</title>
<link rel="stylesheet" href="https://fonts.googleapis.com/css2?family=Questrial&family=Arimo:wght@400;700&display=swap">
<style>
  :root {
    --backdrop: #d6d6d6;
    --paper: #ffffff;
    --ink: #1f1f1f;
    --ink-soft: #4a4a4a;
    --accent-red: #d0201c;
    --rule: #555555;
    --signature-blue: #c9d3ea;
  }
  * { box-sizing: border-box; margin: 0; padding: 0; }
  html, body {
    width: 1200px;
    height: 1000px;
    overflow: hidden;
    background: var(--backdrop);
  }
  .letterhead {
    position: absolute;
    left: 270px;
    top: 33px;
    width: 660px;
    height: 934px;
    background: var(--paper);
    box-shadow: 0 2px 10px rgba(0,0,0,0.12);
    color: var(--ink);
  }
  .brand {
    position: absolute;
    top: 58px;
    left: 0;
    width: 100%;
    display: flex;
    justify-content: center;
    align-items: center;
    gap: 12px;
  }
  .brand-dot {
    width: 22px;
    height: 22px;
    border-radius: 50%;
    background: var(--accent-red);
  }
  .brand-name {
    font-family: "Questrial", sans-serif;
    color: var(--ink);
    text-align: center;
    line-height: 1.15;
    letter-spacing: 0.06em;
  }
  .brand-name .primary { display: block; font-size: 24px; }
  .brand-name .secondary { display: block; font-size: 11px; letter-spacing: 0.18em; }
  .brand-name .locale { display: block; font-size: 7px; letter-spacing: 0.3em; margin-top: 2px; }

  .letter-body {
    position: absolute;
    top: 290px;
    left: 70px;
    right: 70px;
    font-family: "Arimo", sans-serif;
    font-size: 10px;
    line-height: 1.5;
    color: var(--ink-soft);
    text-align: justify;
  }
  .letter-body p { margin-bottom: 12px; }

  .sign-off {
    position: absolute;
    top: 515px;
    right: 70px;
    font-family: "Arimo", sans-serif;
    text-align: right;
    color: var(--ink-soft);
  }
  .sign-off .closing { font-size: 10px; margin-bottom: 12px; }
  .sign-off .signer { font-size: 11px; font-weight: 700; color: var(--ink); }
  .signature {
    position: absolute;
    top: 525px;
    right: 175px;
    width: 130px;
    height: 46px;
    border-radius: 4px;
    background: var(--signature-blue);
  }

  .footer {
    position: absolute;
    bottom: 70px;
    left: 0;
    width: 100%;
    text-align: center;
  }
  .tagline {
    font-family: "Questrial", sans-serif;
    font-size: 17px;
    letter-spacing: 0.02em;
    color: var(--ink);
  }
  .footer-rule {
    width: 370px;
    height: 1px;
    margin: 5px auto 8px;
    background: var(--rule);
  }
  .address, .contacts {
    font-family: "Arimo", sans-serif;
    font-size: 10px;
    color: var(--ink);
  }
  .address { margin-bottom: 4px; }
  .contacts strong { font-weight: 700; }
  .separator {
    display: inline-block;
    width: 5px;
    height: 5px;
    border-radius: 50%;
    background: var(--accent-red);
    margin: 0 6px;
    vertical-align: middle;
  }
  .web { font-weight: 700; }
</style>
</head>
<body>
  <main class="letterhead">
    <header class="brand">
      <span class="brand-dot"></span>
      <div class="brand-name">
        <span class="primary">CORVAN'S</span>
        <span class="secondary">ENTERTAINMENT</span>
        <span class="locale">SRI LANKA</span>
      </div>
    </header>

    <section class="letter-body">
      <p>We are pleased to confirm your membership with our private gaming lounge in Colombo. Your account has been activated and all guest privileges are now available at the main floor, the poker room and the terrace bar. Our hosts will gladly arrange tables and dining at your convenience.</p>
      <p>Please present this letter at the reception desk on your next visit to collect your welcome card and complimentary chips.</p>
      <p>Our team remains available every day and night for any questions regarding events, reservations or your account.</p>
      <p>We thank you for choosing us and look forward to welcoming you again very soon at our tables.</p>
    </section>

    <div class="signature" role="img" aria-label="Handwritten signature of Rila Danent in blue ink"></div>
    <div class="sign-off">
      <p class="closing">Yours Sincerely,</p>
      <p class="signer">Rila Danent</p>
    </div>

    <footer class="footer">
      <p class="tagline">THE FINEST GAMING EXPERIENCE IN THE CITY</p>
      <div class="footer-rule"></div>
      <p class="address">52, Lotus Crescent Road, Colombo 01000, Sri Lanka</p>
      <p class="contacts">
        <strong>Tel:</strong> + 94 11 2000481<span class="separator"></span><strong>Fax:</strong> + 94 11 2000482<span class="separator"></span><span class="web">www.corvanscolombo.com</span>
      </p>
    </footer>
  </main>
</body>
</html>
```